Help design website for "Brightwater Civic Advisors" to advance the common good

Here is the Google doc link that lays out the design:

https://files.plumrivet.example/sheet/d/7QmTzR2wLx9KpVbN4hJcY8sEaUoFdG3iXkMnPq5rWt6/edit?usp=sharing

Here is the Google drive folder with the logos and photos: https://vault.plumrivet.example/open?id=4HkWp9LzQe2TxRvN8mBaYc3DsUoJfG6

The testimonials are being gathered and will be shared by Friday, 1/4.

The winner will also have to migrate the coding files to my hosting site.

Thank you for your help! Looking forward to seeing your designs.

Target Market(s)

Prospective clients

Industry/Entity Type

Non Profit

Coding

Coded - Design and coding required

Number of Pages Required

5+ page

Requirements
Must have
• Noted in the Google doc regarding layout.
Nice to have

```html
<!DOCTYPE html>
<html lang="en">
<head>
<meta charset="utf-8">
<title>Brightwater Civic Advisors — Media &amp; Impact</title>
<link href="https://fonts.googleapis.com/css2?family=Poppins:wght@400;600;700&family=Open+Sans:wght@400;600&display=swap" rel="stylesheet">
<style>
:root{
  --blue:#3b87cc;
  --ink:#111;
  --body:#333;
  --white:#fff;
  --footer:#25262d;
  --hero-a:#8b7f72;
  --hero-b:#2f6a55;
  --photo-a:#6b5a4a;
  --photo-b:#c9b9a6;
}
*{margin:0;padding:0;box-sizing:border-box}
html,body{width:690px;height:1200px;overflow:hidden;background:var(--white)}
body{position:relative;font-family:"Open Sans",Arial,sans-serif;color:var(--body)}
.site-header{position:absolute;left:0;top:0;width:690px;height:71px;background:var(--blue)}
.brand{position:absolute;left:83px;top:26px;display:flex;align-items:center;gap:8px;color:var(--white);font:600 14px/18px "Poppins",Arial,sans-serif}
.brand-mark{width:12px;height:12px;background:var(--white)}
.cta-book{position:absolute;left:423px;top:12px;width:184px;height:24px;border:2px solid var(--white);color:var(--white);font:700 8px/20px "Poppins",Arial,sans-serif;text-align:center;text-transform:uppercase}
.main-nav{position:absolute;top:51px;right:83px;display:flex;gap:18px;font:700 8px/12px "Poppins",Arial,sans-serif;color:var(--white);text-transform:uppercase}
.main-nav .current{border-bottom:1px solid var(--white)}
.hero{position:absolute;left:0;top:71px;width:690px;height:314px;background:linear-gradient(180deg,var(--hero-b) 0%,var(--hero-a) 60%,#cfc3b3 100%)}
.hero-edge{position:absolute;left:0;top:320px;width:690px;height:70px}
.section-title{position:absolute;left:0;top:366px;width:690px;text-align:center;font:700 18px/24px "Poppins",Arial,sans-serif;color:var(--ink)}
.title-rule{position:absolute;left:337px;top:396px;width:16px;height:2px;background:var(--blue)}
.article-card{position:absolute;top:436px;width:251px;height:493px;background:var(--white);box-shadow:0 2px 8px rgba(0,0,0,.14)}
.card-left{left:82px}.card-right{left:354px}
.card-photo{position:relative;width:251px;height:205px;background:linear-gradient(180deg,var(--photo-b),var(--photo-a) 70%,#1c1c1c)}
.card-right .card-photo{background:linear-gradient(180deg,#3d7a62,#a8998a 65%,#1c1c1c)}
.photo-caption{position:absolute;left:17px;bottom:12px;color:var(--white);font:700 8px/10px "Poppins",Arial,sans-serif;text-transform:uppercase}
.card-body{padding:23px 8px 0 17px;height:260px;overflow:hidden}
.card-title{font:600 9.6px/13px "Poppins",Arial,sans-serif;color:var(--ink);margin-bottom:10px;white-space:nowrap}
.card-body p{font-size:7.4px;line-height:10px;margin-bottom:9px;padding-left:2px;padding-right:9px}
.btn-read{position:absolute;left:20px;top:450px;width:70px;height:22px;background:var(--blue);color:var(--white);font:700 8px/22px "Poppins",Arial,sans-serif;text-align:center;text-transform:uppercase}
.btn-all{position:absolute;left:294px;top:965px;width:101px;height:22px;background:var(--blue);color:var(--white);font:700 8px/22px "Poppins",Arial,sans-serif;text-align:center;text-transform:uppercase}
.site-footer{position:absolute;left:0;top:1020px;width:690px;height:180px}
.footer-brand{position:absolute;left:83px;top:1126px;display:flex;align-items:center;gap:9px;color:var(--white);font:600 15px/20px "Poppins",Arial,sans-serif}
.footer-brand .brand-mark{width:13px;height:13px;background:var(--blue)}
.footer-divider{position:absolute;left:351px;top:1096px;width:1px;height:82px;background:#4a4b52}
.footer-menu-label{position:absolute;left:386px;top:1105px;font:700 7px/10px "Poppins",Arial,sans-serif;color:var(--white)}
.footer-links{position:absolute;left:386px;top:1124px;font-size:6.6px;line-height:10px;color:var(--white);text-transform:uppercase}
.footer-links span{margin:0 5px}
.copyright{position:absolute;left:386px;top:1160px;font-size:6.4px;color:var(--white)}
</style>
</head>
<body>
<header class="site-header">
  <div class="brand"><span class="brand-mark"></span><span>Brightwater Civic Advisors</span></div>
  <div class="cta-book">Book a complimentary consultation</div>
  <nav class="main-nav"><span>About</span><span>Services &amp; Testimonials</span><span class="current">Media &amp; Impact</span><span>Contact</span></nav>
</header>

<div class="hero" role="img" aria-label="Photo of a youth band performing in a school gym"></div>
<svg class="hero-edge" viewBox="0 0 690 70" width="690" height="70" aria-hidden="true">
  <polygon points="0,64 345,6 690,64 690,70 0,70" fill="var(--blue)"/>
  <polygon points="0,70 345,12 690,70" fill="var(--white)"/>
</svg>

<h1 class="section-title">Articles</h1>
<div class="title-rule"></div>

<article class="article-card card-left">
  <div class="card-photo" role="img" aria-label="Photo of attendees at round tables listening to a speaker">
    <div class="photo-caption">Attendees listening to a speaker at<br>the Northgate dinner dialogue event</div>
  </div>
  <div class="card-body">
    <h2 class="card-title">Residents Meet With Employment Nonprofit</h2>
    <p>Students and East Side community members attended a "Dinner Dialogue" recently featuring the nonprofit Northgate Jobs Alliance. Conversation centered around the work done by the Alliance to help East Side residents break the cycle of poverty and unemployment.</p>
    <p>The Dinner Dialogue series, created by the Campus Civic Service Office in 2017, seeks to promote the discussion of social justice issues. The meals are hosted three times a quarter at different East Side partner organizations, and are open to the public.</p>
    <p>Four of the attendees included Lena Vargas, a Campus Safety officer and graduate student at the Alder School; Daria Holt, a former Northgate volunteer; and two University students, second-year Mira Kovalenko and third-year Rohan Desai.</p>
  </div>
  <div class="btn-read">Read more</div>
</article>

<article class="article-card card-right">
  <div class="card-photo" role="img" aria-label="Photo of students performing at a park arts festival">
    <div class="photo-caption">Students performing at the third annual<br>Linden Park arts festival</div>
  </div>
  <div class="card-body">
    <h2 class="card-title">Community and Student Arts Shine<br>at Linden Park</h2>
    <p>Every year it gets bigger and better," said Janelle Brooks-Reed, Chief Program Officer of Riverton Youth Programs (RYP), about the third annual Linden Park Arts Festival that took place last Saturday. A collaboration between RYP, Student Government, the Campus Civic Service Office, and several other university and Linden Park community organizations, the annual festival once again provided local East Side entrepreneurs, residents, and Riverton University students with a place to connect and showcase their artistic skills. The festival was held in the building of Riverton Youth Programs, with a central performance space encircled by booths of local retail vendors.</p>
    <p>Throughout the afternoon, vendors such as Maplecrumb Dessert Shop and Hazel's Kitchen provided free food for the event while schoolkids ran around the space, sitting down periodically to watch performances.</p>
  </div>
  <div class="btn-read">Read more</div>
</article>

<div class="btn-all">View all articles</div>

<svg class="site-footer" viewBox="0 0 690 180" width="690" height="180" aria-hidden="true">
  <polygon points="0,62 345,2 690,62 690,180 0,180" fill="var(--footer)"/>
</svg>
<div class="footer-brand"><span class="brand-mark"></span><span>Brightwater Civic Advisors</span></div>
<div class="footer-divider"></div>
<div class="footer-menu-label">MENU</div>
<div class="footer-links">About<span>|</span>Services &amp; Testimonials<span>|</span>Media &amp; Impact<span>|</span>Contact</div>
<div class="copyright">Copyrights @ 2019 All Rights Reserved</div>
</body>
</html>
```